Business Card Design

We like to use greens as you will see in our logo (but not TOO much green). We are a Dental Clinic in a somewhat eccentric community. We do not like the dated sharp designs which we see many dentists use. We're looking for something bright and fresh while still maintaining the integrity of the profession. Elegance is not necessarily what we are going for... we need for the design to be "mature" but also up-lifting.

See our logo.
Updates

Project Deadline Extended
Reason: We have 5 designs which we like. But we'd like to see a few more before committing to a design.

Project Deadline Extended
Reason: We are awaiting revisions to this project. We are still welcoming designs while we wait to see if designers are able to provide to us the revisions we require in order to proceed with a selection.

Target Market(s)

Younger families - ages late 20's to early 40's

Industry/Entity Type

Business

Contact Information for Business Card

Corwel T. Banfry DDS 2730 W. Halvert Rd. Ste. 7 Royal Oak, MI 48391 (248)555-0174 FX (248)555-0189 info@BrightwellDentalCareMi.com BrigthwellDentalCareMi.com on the back of the card we need an appointment reminder (For____ Date___ Time____) with "If you are unable to keep your appointment, kindly give 48 hours notice" at the bottom. No use of teeth in the design. DOUBLE SIDED DESIGN

Requirements
Should not have
• The use of pictures of teeth

```html
<!DOCTYPE html>
<html lang="en">
<head>
<meta charset="utf-8">
<title>Brightwell Dental Care — Business Card</title>
<link href="https://fonts.googleapis.com/css2?family=Roboto+Condensed:wght@400;500;700&display=swap" rel="stylesheet">
<style>
  :root {
    --bg: #2b2b2b;
    --green: #2fa149;
    --green-light: #6cc24a;
    --green-dark: #1f6b37;
    --ink: #2d2d2d;
    --white: #ffffff;
  }
  * { margin: 0; padding: 0; box-sizing: border-box; }
  html, body { width: 1000px; height: 1200px; overflow: hidden; background: var(--bg); }
  body { position: relative; font-family: "Roboto Condensed", "Arial Narrow", sans-serif; }

  .card {
    position: absolute;
    width: 722px;
    height: 423px;
    overflow: hidden;
    background: var(--green);
  }
  .card-front { left: 145px; top: 72px; }
  .card-back { left: 139px; top: 637px; }
  .card-art { position: absolute; inset: 0; width: 100%; height: 100%; }

  /* Front */
  .brand {
    position: absolute;
    left: 70px;
    top: 150px;
    display: flex;
    align-items: center;
    gap: 12px;
  }
  .brand-dot { width: 34px; height: 34px; border-radius: 50%; background: var(--green-light); }
  .brand-name {
    color: var(--green-dark);
    font-weight: 500;
    font-size: 32px;
    line-height: 1.05;
  }
  .identity {
    position: absolute;
    right: 74px;
    top: 114px;
    text-align: right;
  }
  .identity-name { font-weight: 700; font-size: 29px; color: #111; line-height: 1.1; }
  .identity-title { font-weight: 500; font-size: 18px; color: var(--green); margin-top: 4px; }

  .contacts {
    position: absolute;
    right: 32px;
    top: 216px;
    list-style: none;
  }
  .contact {
    display: flex;
    justify-content: flex-end;
    align-items: center;
    gap: 14px;
    font-size: 19px;
    font-weight: 500;
    color: var(--ink);
    height: 30px;
    margin-bottom: 6px;
  }
  .contact:nth-child(3) { margin-top: 8px; }
  .contact-icon {
    width: 28px; height: 28px;
    border-radius: 50%;
    background: var(--green);
    border: 2px solid var(--white);
    box-shadow: 0 0 0 1px var(--green);
    display: flex; align-items: center; justify-content: center;
    flex: none;
  }
  .contact-icon svg { width: 15px; height: 15px; }

  /* Back */
  .back-seal {
    position: absolute;
    left: 517px; top: 43px;
    width: 124px; height: 124px;
    border-radius: 50%;
    border: 3px solid var(--white);
    background: radial-gradient(circle at 40% 35%, #a8d56a, var(--green-light) 45%, #3a9a55 100%);
  }
  .reminder-fields {
    position: absolute;
    left: 68px; right: 66px;
    top: 186px;
    display: flex;
    align-items: flex-end;
    font-weight: 700;
    font-size: 19px;
    color: #111;
  }
  .field-line { border-bottom: 1px solid #555; height: 22px; margin-left: 2px; }
  .field-line.for { width: 202px; }
  .field-line.date { width: 157px; }
  .field-line.time { width: 93px; }
  .notice {
    position: absolute;
    left: 0; right: 0;
    top: 242px;
    text-align: center;
    color: var(--green-dark);
    font-weight: 500;
    font-size: 27px;
    line-height: 34px;
  }
  .address {
    position: absolute;
    left: 0; right: 0;
    top: 334px;
    display: flex;
    justify-content: center;
    align-items: center;
    gap: 6px;
    font-size: 18px;
    color: var(--ink);
  }
  .address-pin {
    width: 27px; height: 27px; border-radius: 50%;
    background: var(--green);
    display: flex; align-items: center; justify-content: center;
  }
  .address-pin svg { width: 14px; height: 16px; }
</style>
</head>
<body>

<section class="card card-front" aria-label="Business card front">
  <svg class="card-art" viewBox="0 0 722 423" aria-hidden="true">
    <rect width="722" height="423" fill="var(--green)"/>
    <ellipse cx="362" cy="211" rx="338" ry="370" fill="var(--green-light)"/>
    <ellipse cx="362" cy="211" rx="322" ry="353" fill="var(--white)"/>
  </svg>

  <div class="brand">
    <span class="brand-dot"></span>
    <span class="brand-name">Brightwell<br>Dental Care</span>
  </div>

  <div class="identity">
    <p class="identity-name">Corwel T. Banfry</p>
    <p class="identity-title">DDS</p>
  </div>

  <ul class="contacts">
    <li class="contact">(248) 555-0174
      <span class="contact-icon"><svg viewBox="0 0 16 16"><path fill="#fff" d="M3.6 1.5l2.3 2.6-1.2 1.7c.8 1.9 2.5 3.6 4.4 4.4l1.7-1.2 2.6 2.3-1.3 2.3C7.5 13.8 2.2 8.5 1.5 3z"/></svg></span>
    </li>
    <li class="contact">(248) 555-0189
      <span class="contact-icon"><svg viewBox="0 0 16 16"><rect x="4" y="2" width="8" height="4" fill="#fff"/><rect x="1.5" y="6" width="13" height="6" rx="1" fill="#fff"/><rect x="4" y="9" width="8" height="5" fill="#fff" stroke="var(--green)" stroke-width="1"/></svg></span>
    </li>
    <li class="contact">info@BrightwellDentalCareMi.com
      <span class="contact-icon"><svg viewBox="0 0 16 16"><rect x="1.5" y="3.5" width="13" height="9" fill="#fff"/><path d="M1.5 3.5L8 9l6.5-5.5" fill="none" stroke="var(--green)" stroke-width="1.2"/></svg></span>
    </li>
    <li class="contact">BrigthwellDentalCareMi.com
      <span class="contact-icon"><svg viewBox="0 0 16 16"><circle cx="8" cy="8" r="6.5" fill="none" stroke="#fff" stroke-width="1.5"/><path d="M1.5 8h13M8 1.5c2.5 2 2.5 11 0 13M8 1.5c-2.5 2-2.5 11 0 13" fill="none" stroke="#fff" stroke-width="1.2"/></svg></span>
    </li>
  </ul>
</section>

<section class="card card-back" aria-label="Business card back, appointment reminder">
  <svg class="card-art" viewBox="0 0 723 423" aria-hidden="true">
    <rect width="723" height="423" fill="var(--green)"/>
    <ellipse cx="392" cy="565" rx="600" ry="526" fill="var(--green-light)"/>
    <ellipse cx="392" cy="565" rx="584" ry="512" fill="var(--white)"/>
  </svg>

  <div class="back-seal"></div>

  <div class="reminder-fields">
    (For<span class="field-line for"></span>
    Date:<span class="field-line date"></span>
    Time:<span class="field-line time"></span>)
  </div>

  <p class="notice">If you are unable to keep your appointment,<br>kindly give 48 hours notice</p>

  <p class="address">
    <span class="address-pin"><svg viewBox="0 0 14 16"><path fill="#fff" d="M7 0a5.5 5.5 0 0 0-5.5 5.5C1.5 9.6 7 16 7 16s5.5-6.4 5.5-10.5A5.5 5.5 0 0 0 7 0zm0 7.6a2.1 2.1 0 1 1 0-4.2 2.1 2.1 0 0 1 0 4.2z"/></svg></span>
    2730 W. Halvert Rd. Ste. 7 Royal Oak, MI 48391
  </p>
</section>

</body>
</html>
```